Allied Health team of Physiotherapists & Occupational Therapists seek a business card design

We have our new logo, we now need our new business cards and stationary. Tidewell: Oedema & Family Clinic is seeking a generic card design to represent our whole team and individual cards for each therapist that incorporates our new logo to communicate our holistic approach that is calming, nuturing, supportive and welcoming.
Our Physiotherapists and Occupational Therapists assess, treat and provide education for people who are at risk of or who have lymphoedema. This is often as a result of treatment for cancer. We provide pre-operative and post-operative management and cancer rehabilitation in our Pilates studio. Our team also consists of Physiotherapists who have a strong interest in pelvic floor and continence management for both men and women.

Target Market(s)

Mainly women health conscious

Industry/Entity Type

Allied Health: Physiotherapy / Occupational Therapy

Contact Information for Business Card

Address: 14 Gallivant Ave Marlowe Bay 3277 Phone: 84316570 fax: 8431 6578 Email: info@tidewellcareservices.com.au Website: tidewellcareservices.com.au Facebook address: facebook.com/TidewellOedemaAndFamilyCareClinic. Room to write appointments. Individual cards need to have name, office email and individual email and professional details

Requirements
Must have
• Logo as per uploaded documents

```html
<!DOCTYPE html>
<html lang="en">
<head>
<meta charset="utf-8">
<title>Tidewell Business Cards</title>
<link href="https://fonts.googleapis.com/css2?family=Montserrat:wght@300;400;500;600;700&display=swap" rel="stylesheet">
<style>
  :root {
    --backdrop: #b4b5b8;
    --card-light: #e6e7ec;
    --peach: #dd9a6f;
    --peach-deep: #d58e62;
    --sage: #98a39a;
    --rule: #8d8f95;
    --white: #ffffff;
  }
  * { box-sizing: border-box; margin: 0; padding: 0; }
  html, body { width: 1200px; height: 900px; overflow: hidden; }
  body {
    background: var(--backdrop);
    font-family: "Montserrat", sans-serif;
    position: relative;
  }
  .card {
    position: absolute;
    top: 170px;
    width: 340px;
    height: 560px;
    border-radius: 3px;
    overflow: hidden;
    box-shadow: 0 14px 30px rgba(0,0,0,0.25);
  }
  .card-front { left: 190px; background: var(--card-light); }
  .card-back { left: 670px; background: linear-gradient(160deg, var(--peach), var(--peach-deep)); }
  .card-shape { position: absolute; inset: 0; }

  .brand {
    position: absolute;
    display: flex;
    align-items: center;
    gap: 8px;
    font-weight: 500;
    font-size: 22px;
    letter-spacing: 0.5px;
  }
  .brand-dot { width: 12px; height: 12px; border-radius: 50%; }
  .card-front .brand { top: 70px; left: 38px; color: var(--peach); }
  .card-front .brand-dot { background: var(--peach); }
  .card-back .brand { top: 80px; left: 0; right: 0; justify-content: center; color: var(--white); }
  .card-back .brand-dot { background: var(--white); }
  .brand-tagline {
    position: absolute;
    font-size: 8.5px;
    letter-spacing: 1.6px;
    text-transform: uppercase;
  }
  .card-front .brand-tagline { top: 104px; left: 40px; color: var(--peach); }
  .card-back .brand-tagline { top: 114px; left: 0; right: 0; text-align: center; color: var(--white); }

  .appointment {
    position: absolute;
    top: 175px;
    left: 34px;
    width: 240px;
    height: 70px;
    border-left: 1px solid var(--rule);
  }
  .appointment-line {
    position: absolute;
    left: 18px;
    right: 0;
    height: 1px;
    background: var(--rule);
  }
  .appointment-line.first { top: 18px; }
  .appointment-line.second { top: 48px; }

  .therapist {
    position: absolute;
    left: 34px;
    bottom: 60px;
    color: var(--white);
  }
  .therapist-name { font-size: 26px; letter-spacing: 0.5px; margin-bottom: 10px; }
  .therapist-name .given { font-weight: 700; }
  .therapist-name .family { font-weight: 300; }
  .therapist-role { font-size: 11.5px; font-weight: 600; line-height: 1.3; }
  .therapist-rule { width: 190px; height: 1px; background: var(--white); margin-top: 10px; }

  .contact-list {
    position: absolute;
    top: 200px;
    left: 34px;
    list-style: none;
    color: var(--white);
    font-size: 11.5px;
    font-weight: 400;
  }
  .contact-list li {
    display: flex;
    align-items: flex-start;
    gap: 8px;
    margin-bottom: 8px;
    line-height: 1.3;
  }
  .contact-list svg { flex: 0 0 11px; width: 11px; height: 11px; margin-top: 2px; fill: var(--white); }
</style>
</head>
<body>

<section class="card card-front" aria-label="Business card front">
  <svg class="card-shape" viewBox="0 0 340 560" preserveAspectRatio="none">
    <path d="M0 560 V330 H150 C270 330 340 250 340 110 V560 Z" fill="var(--peach)"/>
    <path d="M200 326 C290 300 332 230 334 120" fill="none" stroke="var(--sage)" stroke-width="14" stroke-linecap="round" opacity="0.85" role="img" aria-label="Leaf garland ornament along the curve"/>
  </svg>
  <div class="brand"><span class="brand-dot"></span>Tidewell</div>
  <div class="brand-tagline">Oedema &amp; Family Clinic</div>
  <div class="appointment" aria-label="Space to write appointment">
    <span class="appointment-line first"></span>
    <span class="appointment-line second"></span>
  </div>
  <div class="therapist">
    <p class="therapist-name"><span class="given">MARA</span><span class="family">QUINLAN</span></p>
    <p class="therapist-role">Physiotherapist<br>Lymphoedema &amp; Oncology Rehabilitation<br>Continence &amp; Pelvic Floor</p>
    <div class="therapist-rule"></div>
  </div>
</section>

<section class="card card-back" aria-label="Business card back">
  <svg class="card-shape" viewBox="0 0 340 560" preserveAspectRatio="none">
    <path d="M120 470 C240 470 318 390 316 230" fill="none" stroke="var(--white)" stroke-width="12" stroke-linecap="round" opacity="0.3" role="img" aria-label="Faint leaf garland ornament"/>
  </svg>
  <div class="brand"><span class="brand-dot"></span>Tidewell</div>
  <div class="brand-tagline">Oedema &amp; Family Clinic</div>
  <ul class="contact-list">
    <li><svg viewBox="0 0 12 12"><path d="M6 1 L11 6 H9.5 V11 H7 V8 H5 V11 H2.5 V6 H1 Z"/></svg>14 Gallivant Ave, Marlowe Bay 3277</li>
    <li><svg viewBox="0 0 12 12"><rect x="1" y="3" width="10" height="8" rx="1"/><rect x="3" y="1" width="6" height="3"/></svg>8431 6570</li>
    <li><svg viewBox="0 0 12 12"><path d="M2 1 L4.5 1 L5.5 4 L4 5 C5 7 6 8 8 9 L9 7.5 L11 8.5 L11 11 C6 11 1 6 2 1 Z"/></svg>8431 6578</li>
    <li><svg viewBox="0 0 12 12"><rect x="1" y="2.5" width="10" height="7.5" rx="1"/></svg>info@tidewellcareservices.com.au</li>
    <li><svg viewBox="0 0 12 12"><circle cx="6" cy="6" r="5"/></svg>tidewellcareservices.com.au</li>
    <li><svg viewBox="0 0 12 12"><rect x="1" y="1" width="10" height="10" rx="2"/></svg>/tidewelloedemaand<br>familycareclinic</li>
  </ul>
</section>

</body>
</html>
```